Company Postage Label

Design a postage label that measures: 16cm long x 9cm high with a sticky back to stick on boxes. Similar to the attached from Corvanta Post.

Industry/Entity Type

Motorcycle Part

Colors

Designer to choose colors to be used in the design.

Requirements
Must have
• Company logo and address

```html
<!DOCTYPE html>
<html lang="en">
<head>
<meta charset="utf-8">
<title>Torvale Moto Parts – Postage Label</title>
<link href="https://fonts.googleapis.com/css2?family=Allura&family=Arimo:wght@400;700&display=swap" rel="stylesheet">
<style>
  :root{
    --bg:#ece8e1;
    --card:#fbfbf9;
    --ink:#1c1c1c;
    --rule:#2a2a2a;
    --accent:#c4161c;
    --muted:#3a3a3a;
  }
  *{box-sizing:border-box;margin:0;padding:0}
  html,body{width:1200px;height:800px;overflow:hidden;background:var(--bg)}
  .label{
    position:absolute;left:80px;top:107px;width:1040px;height:585px;
    background:var(--card);box-shadow:0 2px 10px rgba(0,0,0,.12);overflow:hidden;
  }
  .message{
    position:absolute;left:48px;top:165px;width:470px;
    font-family:"Allura",cursive;font-size:25px;line-height:29px;color:var(--ink);
  }
  .brand{
    position:absolute;left:420px;top:40px;display:flex;align-items:center;gap:8px;
    font-family:"Arimo",sans-serif;font-weight:700;font-size:15px;color:var(--accent);
    letter-spacing:.5px;text-transform:uppercase;
  }
  .brand-dot{width:14px;height:14px;border-radius:50%;background:var(--accent)}
  .sender-address{
    position:absolute;left:556px;top:90px;writing-mode:vertical-rl;
    font-family:"Arimo",sans-serif;font-size:12px;color:var(--muted);letter-spacing:.3px;
  }
  .stamp-box{position:absolute;left:860px;top:34px;width:120px;height:92px;border:2px solid var(--rule)}
  .address-lines{position:absolute;left:600px;top:0;width:400px;height:585px}
  .website{
    position:absolute;left:600px;top:528px;
    font-family:"Arimo",sans-serif;font-size:15px;letter-spacing:.6px;color:var(--muted);
  }
</style>
</head>
<body>
  <section class="label">
    <p class="message">Where does it come from? Every part we ship is packed by hand in our workshop and checked twice before it leaves the bench. Our team has spent many years riding, fixing and rebuilding bikes of every size, so we know how much a single bolt can matter on the road. Thank you for choosing us for your next build. Inside this parcel you will find the parts you ordered, a packing slip and a short note with fitting tips. If anything is missing or damaged, reply to your order email within seven days and we will make it right. Ride safe, keep the rubber side down and enjoy the journey ahead.</p>

    <div class="brand"><span class="brand-dot"></span>Torvale Moto Parts</div>
    <div class="sender-address">18 Fenwick Road, Harlow Creek, QLD 4190</div>

    <div class="stamp-box"></div>

    <svg class="address-lines" viewBox="0 0 400 585" aria-hidden="true">
      <g stroke="var(--rule)" stroke-width="2" fill="none">
        <line x1="0" y1="190" x2="400" y2="190"/>
        <line x1="0" y1="255" x2="400" y2="255"/>
        <line x1="0" y1="320" x2="400" y2="320"/>
        <line x1="0" y1="385" x2="400" y2="385"/>
        <rect x="260" y="400" width="35" height="40"/>
        <rect x="295" y="400" width="35" height="40"/>
        <rect x="330" y="400" width="35" height="40"/>
        <rect x="365" y="400" width="35" height="40"/>
        <line x1="0" y1="440" x2="400" y2="440"/>
        <line x1="0" y1="510" x2="400" y2="510"/>
      </g>
    </svg>

    <div class="website">WWW.TORVALEMOTO.COM</div>
  </section>
</body>
</html>
```